Commercial and Residential Paint Contractor needs website

We need a website for our residential painting, multi-family painting and commercial painting company. We paint interior and exterior of houses, apartments and commercial buildings. I would like an about us page, residential page, multi family page, commercial page and contact us. Need keywords added to website for seo opitimazation. I like this website https://www.wallcraftcrew.com/

Target Market(s)

General Contractors and commercial property managers

Coding

Coded - Design and coding required

Number of Pages Required

5+ page

Font styles to use
Sans Serif

Requirements
Must have
• I need SEO keywords on pages

```html
<!DOCTYPE html>
<html lang="en">
<head>
<meta charset="utf-8">
<title>Hartline Painting – Commercial &amp; Residential Painting</title>
<meta name="description" content="Hartline Painting: residential painting, multi-family painting and commercial painting contractor for interior and exterior of houses, apartments and commercial buildings.">
<link rel="stylesheet" href="https://fonts.googleapis.com/css2?family=Lato:wght@400;700;900&family=Montserrat:wght@700;800&display=swap">
<style>
:root{
  --navy:#173a7f;
  --red:#c0182f;
  --ink:#222;
  --text:#333;
  --grey-bg:#efefef;
  --white:#fff;
  --footer:#111;
}
*{box-sizing:border-box;margin:0;padding:0}
html,body{width:1200px;height:4975px;overflow:hidden}
body{font-family:'Lato',sans-serif;color:var(--text);background:var(--white);position:relative}
.photo{position:absolute;display:block}
h2.section-title{position:absolute;left:0;width:1200px;text-align:center;font:700 33px 'Lato',sans-serif;color:var(--navy)}
.btn-outline{position:absolute;display:flex;align-items:center;justify-content:center;border:2px solid var(--red);color:var(--red);font:700 16px 'Lato',sans-serif;text-transform:uppercase;background:var(--white)}

/* header */
.site-header{position:absolute;top:0;left:0;width:1200px;height:85px;background:var(--white)}
.brand{position:absolute;left:77px;top:20px;display:flex;align-items:center;gap:10px;font:900 34px 'Lato',sans-serif;color:var(--navy);letter-spacing:-.5px}
.brand-mark{width:16px;height:16px;background:var(--red)}
.call{position:absolute;right:34px;top:26px;display:flex;align-items:center;gap:12px;font:700 16px 'Lato',sans-serif;color:var(--ink)}
.call .num{font-size:22px;color:var(--red);margin-left:6px}
.call-icon{width:36px;height:36px;border-radius:50%;background:var(--red);display:flex;align-items:center;justify-content:center}

.main-nav{position:absolute;top:85px;left:0;width:1200px;height:47px;background:var(--navy)}
.main-nav ul{list-style:none;position:absolute;left:214px;top:0;height:47px;display:flex}
.main-nav li{height:47px;display:flex;align-items:center;padding:0 21px;color:var(--white);font:700 14px 'Lato',sans-serif;text-transform:uppercase}
.main-nav li.active{background:var(--red)}

/* hero */
.hero{position:absolute;top:132px;left:0;width:1200px;height:603px;background:linear-gradient(90deg,#cfd9d9 0%,#dfe6e4 45%,#e7dcd6 100%)}
.hero-copy{position:absolute;left:74px;top:168px}
.hero-copy .kicker{font:800 54px/1 'Montserrat',sans-serif;color:var(--navy)}
.hero-copy h1{font:800 68px/1.05 'Montserrat',sans-serif;color:var(--navy);margin-top:2px}
.hero-copy .sub{font:700 31px 'Lato',sans-serif;color:var(--ink);margin-top:6px}
.btn-solid{position:absolute;left:74px;top:374px;width:181px;height:54px;background:var(--red);color:var(--white);display:flex;align-items:center;justify-content:center;font:700 18px 'Lato',sans-serif;text-transform:uppercase}
.dots{position:absolute;left:556px;top:562px;display:flex;gap:10px}
.dots span{width:12px;height:12px;border-radius:50%;background:#bbb}
.dots span:first-child{background:#fff}

/* about */
.about p{position:absolute;left:105px;width:990px;top:855px;text-align:center;font:400 16px/29px 'Lato',sans-serif;color:var(--ink)}

/* services */
.services{position:absolute;top:1115px;left:0;width:1200px;height:726px;background:var(--grey-bg)}
.service-card{position:absolute;left:342px;width:784px;height:178px;background:var(--white);box-shadow:0 2px 10px rgba(0,0,0,.18)}
.service-card .photo{left:14px;top:14px;width:282px;height:150px}
.service-card h3{position:absolute;left:324px;top:16px;font:700 25px 'Lato',sans-serif;color:var(--navy)}
.service-card p{position:absolute;left:324px;top:54px;width:430px;font:400 13.5px/26px 'Lato',sans-serif;color:var(--ink)}
.service-card a{position:absolute;left:324px;top:142px;font:700 13px 'Lato',sans-serif;color:var(--red);text-decoration:none}

/* area */
.area-card{position:absolute;top:1982px;width:512px}
.area-card .photo{left:0;top:0;width:512px;height:367px}
.area-card .caption{position:absolute;left:24px;top:300px;width:464px;background:var(--white);padding-top:20px;text-align:center;font:700 23px/32px 'Lato',sans-serif;color:var(--navy)}
.area-card p{position:absolute;left:44px;top:404px;width:424px;text-align:center;font:400 16.5px/28px 'Lato',sans-serif;color:var(--ink)}
.area-card .btn-outline{left:166px;top:535px;width:180px;height:55px}

/* gallery */
.gallery{position:absolute;top:2641px;left:0;width:1200px;height:556px;background:var(--grey-bg)}

/* testimonials */
.testimonials{position:absolute;top:3197px;left:0;width:1200px;height:354px;background:linear-gradient(90deg,#1b3a7d 0%,#4a2a6e 50%,#b8172d 100%);color:var(--white)}
.testimonials h2{position:absolute;left:0;width:1200px;top:42px;text-align:center;font:700 33px 'Lato',sans-serif}
.avatar{position:absolute;left:168px;top:115px;width:170px;height:170px;border-radius:50%;border:5px solid var(--white);background:linear-gradient(135deg,#c9a98c,#8a6b58)}
.quote{position:absolute;left:404px;top:109px;width:612px;font:400 16.5px/29px 'Lato',sans-serif}
.quote-name{position:absolute;left:404px;top:265px;font:700 18px 'Lato',sans-serif}
.arrow{position:absolute;top:185px}

/* news */
.news-card{position:absolute;top:3677px;width:331px}
.news-card .photo{left:0;top:0;width:331px;height:212px}
.news-card .caption{position:absolute;left:16px;top:174px;width:299px;background:var(--white);padding-top:12px;text-align:center}
.news-card h3{font:700 23px/29px 'Lato',sans-serif;color:var(--ink)}
.news-card time{display:block;font:700 14px 'Lato',sans-serif;color:var(--red);margin-top:6px}
.news-card p{width:232px;margin:6px auto 0;font:400 16.5px/26px 'Lato',sans-serif;color:var(--ink)}

/* contact */
.contact-card{position:absolute;left:73px;top:4169px;width:723px;height:526px;background:var(--white);box-shadow:0 2px 14px rgba(0,0,0,.2)}
.contact-card h2{position:absolute;left:39px;top:38px;font:700 33px 'Lato',sans-serif;color:var(--navy)}
.contact-line{position:absolute;left:39px;display:flex;align-items:center;gap:12px;font:400 15px 'Lato',sans-serif;color:var(--ink)}
.field{position:absolute;height:56px;border:1px solid #999;background:var(--white);font:400 13px 'Lato',sans-serif;color:var(--ink);padding:18px 16px;display:flex;align-items:center;justify-content:space-between}
.field.msg{align-items:flex-start;padding-top:14px}
.submit{position:absolute;left:39px;top:428px;width:180px;height:54px;background:var(--red);color:var(--white);font:700 18px 'Lato',sans-serif;display:flex;align-items:center;justify-content:center}

/* footer */
.site-footer{position:absolute;top:4811px;left:0;width:1200px;height:164px;background:var(--footer);color:var(--white)}
.site-footer ul{list-style:none;position:absolute;left:0;width:1200px;top:32px;display:flex;justify-content:center;gap:42px;font:700 14px 'Lato',sans-serif;text-transform:uppercase}
.copyright{position:absolute;left:0;width:1200px;top:76px;text-align:center;font:400 12px 'Lato',sans-serif;color:#ddd}
.social{position:absolute;left:0;width:1200px;top:106px;display:flex;justify-content:center;gap:22px}
.social span{width:20px;height:20px;border-radius:50%;background:var(--white)}
</style>
</head>
<body>

<header class="site-header">
  <div class="brand"><span class="brand-mark"></span>HARTLINE</div>
  <div class="call">
    <span class="call-icon"><svg width="18" height="18" viewBox="0 0 24 24"><path fill="#fff" d="M6.6 10.8a15 15 0 0 0 6.6 6.6l2.2-2.2c.3-.3.7-.4 1-.2 1.1.4 2.3.6 3.6.6.6 0 1 .4 1 1V20c0 .6-.4 1-1 1A17 17 0 0 1 3 4c0-.6.4-1 1-1h3.5c.6 0 1 .4 1 1 0 1.3.2 2.5.6 3.6.1.3 0 .7-.2 1z"/></svg></span>
    CALL US TODAY: <span class="num">1-800-555-0147</span>
  </div>
</header>

<nav class="main-nav">
  <ul>
    <li class="active">Home</li><li>About Us</li><li>Residential</li><li>Multi Family</li><li>Commercial</li><li>Contact Us</li>
  </ul>
</nav>

<section class="hero">
  <div class="photo" role="img" aria-label="Smiling painter rolling orange paint onto a wall beside a ladder" style="left:520px;top:0;width:680px;height:603px;background:linear-gradient(90deg,rgba(223,230,228,0) 0%,#d8c4b8 40%,#e2cfc6 100%)"></div>
  <div class="hero-copy">
    <div class="kicker">WELCOME TO</div>
    <h1>HARTLINE PAINTING</h1>
    <div class="sub">Commercial &amp; Residential Painting</div>
  </div>
  <div class="btn-solid">Contact Us</div>
  <div class="dots"><span></span><span></span></div>
</section>

<section class="about">
  <h2 class="section-title" style="top:792px">About Hartline Painting</h2>
  <p>Pellentesque habitant morbi tristique senectus et netus et malesuada fames ac turpis egestas. Morbi lobortis nibh sit amet sapien accumsan scelerisque. Sed consectetur efficitur finibus. Maecenas congue turpis ligula, nec malesuada dui sodales eget urabitur convallis arcu a nisi congue, efficitur fermentum dolor tincidunt aliquet</p>
  <div class="btn-outline" style="left:510px;top:980px;width:180px;height:54px">Read More</div>
</section>

<section class="services">
  <div class="photo" role="img" aria-label="Painter in white cap holding a yellow paint roller" style="left:0;top:0;width:497px;height:726px;background:linear-gradient(160deg,#c4d3e0,#9fb6cc 60%,#e8e0cc)"></div>
  <article class="service-card" style="top:67px">
    <div class="photo" role="img" aria-label="Painters working on a pink interior wall" style="background:linear-gradient(120deg,#e9b8c2,#cfd6cf)"></div>
    <h3>Residential Painting</h3>
    <p>Pellentesque habitant morbi tristique senectus et netus et malesuada fames ac turpis egestas. Morbi lobortis nibh sit amet sapien&nbsp; accumsan scelerisque consectetur.</p>
    <a href="#">Learn More</a>
  </article>
  <article class="service-card" style="top:274px">
    <div class="photo" role="img" aria-label="Painter with a roller in a teal apartment room" style="background:linear-gradient(120deg,#5fb2a6,#a7d4cc)"></div>
    <h3>Multi-Family Painting</h3>
    <p>Pellentesque habitant morbi tristique senectus et netus et malesuada fames ac turpis egestas. Morbi lobortis nibh sit amet sapien&nbsp; accumsan scelerisque consectetur.</p>
    <a href="#">Learn More</a>
  </article>
  <article class="service-card" style="top:479px">
    <div class="photo" role="img" aria-label="Rope-access painters coating a commercial building facade" style="background:linear-gradient(120deg,#2f5a86,#5c86a8)"></div>
    <h3>Commercial painting</h3>
    <p>Pellentesque habitant morbi tristique senectus et netus et malesuada fames ac turpis egestas. Morbi lobortis nibh sit amet sapien&nbsp; accumsan scelerisque consectetur.</p>
    <a href="#">Learn More</a>
  </article>
</section>

<section class="area">
  <h2 class="section-title" style="top:1900px">Area We Serves</h2>
  <article class="area-card" style="left:75px">
    <div class="photo" role="img" aria-label="Painter finishing a turquoise interior wall of a house" style="background:linear-gradient(135deg,#6fc8c8,#3ea7b0)"></div>
    <div class="caption">Interior and Exterior<br>of Houses</div>
    <p>Pellentesque habitant morbi tristique senectus et netus et malesuada fames ac turpis egestas lobortis nibh sit amet sapien&nbsp; accumsan scelerisque consectetur efficitur finibus.</p>
    <div class="btn-outline">Read More</div>
  </article>
  <article class="area-card" style="left:614px">
    <div class="photo" role="img" aria-label="Rope-access painters on an apartment building facade" style="background:linear-gradient(135deg,#bcbcc4,#7d8088)"></div>
    <div class="caption">Apartments and Commercial<br>Buildings</div>
    <p>Pellentesque habitant morbi tristique senectus et netus et malesuada fames ac turpis egestas lobortis nibh sit amet sapien&nbsp; accumsan scelerisque consectetur efficitur finibus.</p>
    <div class="btn-outline">Read More</div>
  </article>
</section>

<section class="gallery">
  <h2 class="section-title" style="top:50px">Gallery</h2>
  <div class="photo" role="img" aria-label="Painter rolling a white ceiling" style="left:75px;top:129px;width:242px;height:174px;background:linear-gradient(135deg,#e6e6e6,#bdbdbd)"></div>
  <div class="photo" role="img" aria-label="Painter applying ochre paint to a wall" style="left:332px;top:129px;width:242px;height:174px;background:linear-gradient(135deg,#4a4a4a,#c89a4c)"></div>
  <div class="photo" role="img" aria-label="Two-storey house with autumn trees" style="left:75px;top:322px;width:242px;height:174px;background:linear-gradient(180deg,#c07a3c,#8c6a58 60%,#5e5a48)"></div>
  <div class="photo" role="img" aria-label="Worker spraying plaster on a wall" style="left:332px;top:322px;width:242px;height:174px;background:linear-gradient(135deg,#d7d2ca,#6a6258)"></div>
  <div class="photo" role="img" aria-label="Rope-access painters on a grey building facade" style="left:587px;top:129px;width:539px;height:367px;background:linear-gradient(135deg,#b6b6b8,#5d5f64)"></div>
</section>

<section class="testimonials">
  <h2>Testimonials</h2>
  <svg class="arrow" style="left:104px" width="16" height="28" viewBox="0 0 16 28"><path d="M14 2 2 14l12 12" fill="none" stroke="#fff" stroke-width="2"/></svg>
  <div class="avatar" role="img" aria-label="Portrait of a happy family client"></div>
  <p class="quote">“ Pellentesque habitant morbi tristique senectus et netus et malesuada fames ac turpis&nbsp; egestas. Morbi lobortis nibh sit amet sapien&nbsp; accumsan scelerisque consectetur efficitur&nbsp; finibus. Maecenas congue turpis ligula, nec malesuada dui sodales eget urabitur convallis arcu a nisi congue, efficitur fermentum&nbsp; dolor tincidunt aliquet..”</p>
  <div class="quote-name">Name Heading</div>
  <svg class="arrow" style="left:1088px" width="16" height="28" viewBox="0 0 16 28"><path d="M2 2l12 12L2 26" fill="none" stroke="#fff" stroke-width="2"/></svg>
</section>

<section class="news">
  <h2 class="section-title" style="top:3604px">Latest News</h2>
  <article class="news-card" style="left:75px">
    <div class="photo" role="img" aria-label="Freshly painted colourful apartment tower" style="background:linear-gradient(160deg,#3f76c8,#e3b13d 60%,#c7442e)"></div>
    <div class="caption"><h3>Morbi lobortis nibh<br>sit amet</h3><time>Jan 04, 2020</time><p>Pellentesque habitant morbi tristique senectus et netus et malesuada fames ac.</p></div>
  </article>
  <article class="news-card" style="left:435px">
    <div class="photo" role="img" aria-label="Rope-access painters on a blue facade" style="background:linear-gradient(135deg,#2f5a86,#6d92b0)"></div>
    <div class="caption"><h3>Morbi lobortis nibh<br>sit amet</h3><time>Jan 04, 2020</time><p>Pellentesque habitant morbi tristique senectus et netus et malesuada fames ac.</p></div>
  </article>
  <article class="news-card" style="left:796px">
    <div class="photo" role="img" aria-label="Painters on ladders in a bright interior" style="background:linear-gradient(120deg,#ececec,#d8c3a8)"></div>
    <div class="caption"><h3>Morbi lobortis nibh<br>sit amet</h3><time>Jan 04, 2020</time><p>Pellentesque habitant morbi tristique senectus et netus et malesuada fames ac.</p></div>
  </article>
</section>

<section class="contact">
  <div class="photo" role="img" aria-label="City skyline at sunset beside a river" style="left:703px;top:4129px;width:497px;height:628px;background:linear-gradient(180deg,#8fb3d6 0%,#d8a66a 45%,#3d3a3e 75%,#1d2f40 100%)"></div>
  <div class="contact-card">
    <h2>Contact Us</h2>
    <div class="contact-line" style="top:107px">
      <svg width="12" height="16" viewBox="0 0 12 16"><path fill="#c0182f" d="M6 0a6 6 0 0 0-6 6c0 4.5 6 10 6 10s6-5.5 6-10a6 6 0 0 0-6-6zm0 8.5A2.5 2.5 0 1 1 6 3.5a2.5 2.5 0 0 1 0 5z"/></svg>
      4820 Maple Crest Dr Ste 12 Fairview, Texas 75069, US&nbsp; |&nbsp;
      <svg width="14" height="14" viewBox="0 0 24 24"><path fill="#c0182f" d="M6.6 10.8a15 15 0 0 0 6.6 6.6l2.2-2.2c.3-.3.7-.4 1-.2 1.1.4 2.3.6 3.6.6.6 0 1 .4 1 1V20c0 .6-.4 1-1 1A17 17 0 0 1 3 4c0-.6.4-1 1-1h3.5c.6 0 1 .4 1 1 0 1.3.2 2.5.6 3.6.1.3 0 .7-.2 1z"/></svg>
      1-800-555-0147
    </div>
    <div class="contact-line" style="top:138px">
      <svg width="16" height="12" viewBox="0 0 16 12"><rect width="16" height="12" fill="#c0182f"/><path d="M0 0l8 6 8-6" fill="none" stroke="#fff" stroke-width="1.3"/></svg>
      hello@hartlinecrew.net
    </div>
    <div class="field" style="left:39px;top:173px;width:320px">Name</div>
    <div class="field" style="left:373px;top:173px;width:320px">Email Address</div>
    <div class="field" style="left:39px;top:246px;width:320px">Phone</div>
    <div class="field" style="left:373px;top:246px;width:320px">Select Services
      <svg width="8" height="12" viewBox="0 0 8 12"><path d="M4 0 8 5H0zM4 12 0 7h8z" fill="#222"/></svg></div>
    <div class="field msg" style="left:39px;top:319px;width:654px;height:92px">Message</div>
    <div class="submit">Submit</div>
  </div>
</section>

<footer class="site-footer">
  <ul><li>Home</li><li>About Us</li><li>Residential</li><li>Multi Family</li><li>Commercial</li><li>Contact Us</li></ul>
  <div class="copyright">Copyright © 2020 . Company Name All Right Reserved</div>
  <div class="social" aria-label="Social media links"><span></span><span></span><span></span><span></span><span></span></div>
</footer>

</body>
</html>
```